Fresh, modern, fun business card for pediatric dental practice

Need a business card for fresh, modern, fun pediatric dental practice

Clean look that matches our website's font and colors

We prefer the look of curved corners on business cards

Target Market(s)

parents (mothers) of young children, professionals, mid-high class

Industry/Entity Type

Dental

Contact Information for Business Card

Maplebrook Pediatric Dentistry
482 Quarry Lane
Suite 517
Fernvale, PA 17599
717.555.0193
www.maplebrookkidsdental.example

Mei-Ran Tsai, DMD
Corinne Walbeck, DMD
(we are working on our email address, but we would like that on the card as well)

Font styles to use
Sans Serif

Requirements
Must have
• All info; we would also like to make cards for individual staff members
• colors from our website and color palatte, attatched
• use same font and design as website for branding
Nice to have
• clean, simple card that has a pop of color
• we would like to see a few designs with our tag line "little teeth, big smiles"
• we are not sure if we want to have it on there or not
• we would like to see a few designs incorporating the ribbon graphic on our website where the word WELCOME is

```html
<!DOCTYPE html>
<html lang="en">
<head>
<meta charset="utf-8">
<title>Maplebrook Pediatric Dentistry – Business Cards</title>
<link rel="stylesheet" href="https://fonts.googleapis.com/css2?family=Roboto:wght@400;500&family=Ubuntu:wght@500&family=Lato:wght@400;700&display=swap">
<style>
  :root {
    --magenta: #d02b8f;
    --sun: #f6b21c;
    --ink: #3b3b3b;
    --paper: #ffffff;
    --paper-fade: #f3f3f3;
    --backdrop: #34302e;
  }
  * { margin: 0; padding: 0; box-sizing: border-box; }
  html, body { width: 1200px; height: 960px; overflow: hidden; }
  body { background: var(--backdrop); position: relative; font-family: "Lato", sans-serif; }

  .card {
    position: absolute;
    width: 476px;
    height: 268px;
    border-radius: 12px;
    overflow: hidden;
  }
  .card--front { background: linear-gradient(180deg, var(--paper) 55%, var(--paper-fade) 100%); }
  .card--back { background: var(--magenta); }

  .pos-tl { left: 110px; top: 184px; }
  .pos-tr { left: 611px; top: 184px; }
  .pos-bl { left: 110px; top: 502px; }
  .pos-br { left: 611px; top: 502px; }

  .person {
    position: absolute; left: 27px; top: 61px;
    font-family: "Roboto", sans-serif; font-weight: 500;
    font-size: 19px; color: var(--magenta); letter-spacing: -0.2px;
  }
  .person .degree { color: var(--sun); font-weight: 400; }

  .brand {
    position: absolute; text-align: center;
    font-family: "Ubuntu", sans-serif; font-weight: 500;
    line-height: 1;
  }
  .brand__mark { display: block; margin: 0 auto; border-radius: 50%; }
  .brand__name { display: block; }

  .brand--front { right: 30px; top: 18px; width: 190px; color: var(--sun); }
  .brand--front .brand__mark { width: 22px; height: 22px; background: var(--sun); margin-bottom: 10px; }
  .brand--front .brand__name { font-size: 25px; letter-spacing: 0.5px; }
  .brand--front .brand__sub { display: block; font-size: 13px; letter-spacing: 1px; margin-top: 4px; }

  .brand--back { left: 0; right: 0; color: var(--paper); }
  .brand--back .brand__mark { background: var(--paper); }
  .brand--solid { top: 80px; }
  .brand--solid .brand__mark { width: 28px; height: 28px; margin-bottom: 12px; }
  .brand--solid .brand__name { font-size: 33px; letter-spacing: 1px; }
  .brand--solid .brand__sub { display: block; font-size: 16px; letter-spacing: 1.6px; margin-top: 6px; }

  .pattern-field {
    position: absolute; inset: 0;
    background: radial-gradient(circle at 50% 50%, #d53a93 0%, var(--magenta) 70%);
  }
  .brand--pattern { top: 110px; }
  .brand--pattern .brand__name { font-size: 29px; letter-spacing: 1px; }
  .brand--pattern .brand__sub { display: block; font-size: 14px; letter-spacing: 1.4px; margin-top: 5px; }

  .practice {
    position: absolute; left: 27px; top: 128px;
    font-size: 11px; line-height: 15px; color: var(--ink); font-style: normal;
  }
  .practice__name { color: var(--magenta); font-weight: 700; font-size: 11px; }

  .contact {
    position: absolute; left: 27px; top: 192px;
    list-style: none; font-size: 11px; color: var(--ink);
  }
  .contact li { display: flex; align-items: center; height: 17px; }
  .contact svg { width: 13px; height: 13px; margin-right: 6px; flex: none; }

  .ribbon { position: absolute; right: 0; top: 211px; width: 204px; height: 30px; }
  .ribbon svg { position: absolute; inset: 0; }
  .ribbon__text {
    position: absolute; left: 29px; top: 0; line-height: 30px;
    font-size: 13px; color: var(--paper); white-space: nowrap;
  }
</style>
</head>
<body>

<!-- Front: Dr. Tsai -->
<section class="card card--front pos-tl">
  <h1 class="person">Mei-Ran Tsai, <span class="degree">DMD</span></h1>
  <div class="brand brand--front">
    <span class="brand__mark"></span>
    <span class="brand__name">maplebrook</span>
    <span class="brand__sub">pediatric dentistry</span>
  </div>
  <address class="practice">
    <div class="practice__name">Maplebrook Pediatric Dentistry</div>
    <div>482 Quarry Lane, Suite 517</div>
    <div>Fernvale, PA 17599</div>
  </address>
  <ul class="contact">
    <li><svg viewBox="0 0 14 14"><circle cx="7" cy="7" r="7" fill="var(--magenta)"/><path d="M4.3 3.6l1.6-.3.8 1.9-1 .7a5 5 0 0 0 2.4 2.4l.7-1 1.9.8-.3 1.6c-3.4.3-6.4-2.7-6.1-6.1z" fill="#fff"/></svg>717.555.0193</li>
    <li><svg viewBox="0 0 14 14"><circle cx="7" cy="7" r="7" fill="var(--magenta)"/><rect x="3.5" y="4.5" width="7" height="5" rx=".6" fill="#fff"/><path d="M3.7 4.8L7 7.4l3.3-2.6" stroke="var(--magenta)" stroke-width=".8" fill="none"/></svg>info@maplebrookkidsdental.example</li>
    <li><svg viewBox="0 0 14 14"><circle cx="7" cy="7" r="7" fill="var(--magenta)"/><circle cx="7" cy="7" r="3.6" fill="none" stroke="#fff" stroke-width=".9"/><path d="M3.4 7h7.2M7 3.4c-1.6 2-1.6 5.2 0 7.2M7 3.4c1.6 2 1.6 5.2 0 7.2" stroke="#fff" stroke-width=".8" fill="none"/></svg>www.maplebrookkidsdental.example</li>
  </ul>
  <div class="ribbon">
    <svg viewBox="0 0 204 30" preserveAspectRatio="none"><polygon points="0,0 204,0 204,30 0,30 12,15" fill="var(--magenta)"/></svg>
    <span class="ribbon__text">little teeth, big smiles</span>
  </div>
</section>

<!-- Back: solid -->
<section class="card card--back pos-tr">
  <div class="brand brand--back brand--solid">
    <span class="brand__mark"></span>
    <span class="brand__name">maplebrook</span>
    <span class="brand__sub">pediatric dentistry</span>
  </div>
</section>

<!-- Front: Dr. Walbeck -->
<section class="card card--front pos-bl">
  <h1 class="person">Corinne Walbeck, <span class="degree">DMD</span></h1>
  <div class="brand brand--front">
    <span class="brand__mark"></span>
    <span class="brand__name">maplebrook</span>
    <span class="brand__sub">pediatric dentistry</span>
  </div>
  <address class="practice">
    <div class="practice__name">Maplebrook Pediatric Dentistry</div>
    <div>482 Quarry Lane, Suite 517</div>
    <div>Fernvale, PA 17599</div>
  </address>
  <ul class="contact">
    <li><svg viewBox="0 0 14 14"><circle cx="7" cy="7" r="7" fill="var(--magenta)"/><path d="M4.3 3.6l1.6-.3.8 1.9-1 .7a5 5 0 0 0 2.4 2.4l.7-1 1.9.8-.3 1.6c-3.4.3-6.4-2.7-6.1-6.1z" fill="#fff"/></svg>717.555.0193</li>
    <li><svg viewBox="0 0 14 14"><circle cx="7" cy="7" r="7" fill="var(--magenta)"/><rect x="3.5" y="4.5" width="7" height="5" rx=".6" fill="#fff"/><path d="M3.7 4.8L7 7.4l3.3-2.6" stroke="var(--magenta)" stroke-width=".8" fill="none"/></svg>info@maplebrookkidsdental.example</li>
    <li><svg viewBox="0 0 14 14"><circle cx="7" cy="7" r="7" fill="var(--magenta)"/><circle cx="7" cy="7" r="3.6" fill="none" stroke="#fff" stroke-width=".9"/><path d="M3.4 7h7.2M7 3.4c-1.6 2-1.6 5.2 0 7.2M7 3.4c1.6 2 1.6 5.2 0 7.2" stroke="#fff" stroke-width=".8" fill="none"/></svg>www.maplebrookkidsdental.example</li>
  </ul>
  <div class="ribbon">
    <svg viewBox="0 0 204 30" preserveAspectRatio="none"><polygon points="0,0 204,0 204,30 0,30 12,15" fill="var(--magenta)"/></svg>
    <span class="ribbon__text">little teeth, big smiles</span>
  </div>
</section>

<!-- Back: patterned -->
<section class="card card--back pos-br">
  <div class="pattern-field" role="img" aria-label="Repeating pattern of small orange sun motifs on magenta"></div>
  <div class="brand brand--back brand--pattern">
    <span class="brand__name">maplebrook</span>
    <span class="brand__sub">pediatric dentistry</span>
  </div>
</section>

</body>
</html>
```